A Techincal Author needs a site to promote his Programming Books

The StudyAlong series is a collection of books focusing on building the same app with different technologies. The purpose of this project is to design a web site home page that can be used to sell the books.

Expected Deliverables
• StudyAlong Logo as Illustrator file
• Master graphic design files for any relevant web assets
• HTML and CSS for home page, if applicable

Target Market(s)

The target market for our series is web programmers. They are people who have some experience, but want to learn a new tool. Programmers are analytical, logical people who like structure in the things they do.

Here are some things our customers like:

• Chirply / Postbox
• Crown of Ashes / Hollow Tide / Salt Hollow
• SmartPhones, Tablets, Stridelets, and other tech gadgets.

The design should try to speak to that market.

Requirements
Must have
• The primary tasks for this project are:
• 1) Create "Study Along" Logo.
• * All “NetPivot” properties use a similar logo approach, with the NetPivot ball icon on the left, a reflection below it. The company name is on the right, roughly the same size as the ball icon. A tag line underneath the company name, roughly the same size as the reflection.
• * Company Name: Study Along
• * Tagline: Knowledge to Boost Your Career
• * Logo color is up to the discretion of the designer, but should be compatible with the site design.
• * Sample Logos for other NetPivot properties in Illustrator format are available as attachments to this project.
• 2) Design the Study Along Home Page.
• The home page should follow this format:
• * Logo
• * Nav Bar
• • Buy (The Home Page)
• • About
• • Contact
• * Main Content
• • Home page content detailed in attachment
• * Footer
• • Copyright notice
• • Links to other stuff we do ( net-pivot.example | marlonpeake.example | BeyondTheGrid.example )
Nice to have
• It would be nice to have a book as part of the home page content.
Should not have
• Please do not use the same color scheme as BeyondTheGrid.example or Plumvane.example or QueryTheMaven.example

```html
<!DOCTYPE html>
<html lang="en">
<head>
<meta charset="utf-8">
<title>Study Along – Knowledge to Boost Your Career</title>
<link href="https://fonts.googleapis.com/css2?family=Montserrat:wght@400;500;600;700&display=swap" rel="stylesheet">
<style>
:root{
  --black:#000;
  --red:#a5262a;
  --red-dark:#6b0f12;
  --orange:#fbb111;
  --grey-bg:#efefef;
  --text:#444;
  --white:#fff;
  --line:#ddd;
}
*{box-sizing:border-box;margin:0;padding:0}
html,body{width:876px;height:1200px;overflow:hidden}
body{position:relative;font-family:"Montserrat",sans-serif;color:var(--text);background:var(--white)}
.abs{position:absolute}

.site-header{position:absolute;left:0;top:0;width:876px;height:72px;background:var(--black)}
.brand{position:absolute;left:126px;top:20px;font-size:28px;font-weight:500;color:var(--white);letter-spacing:.3px}
.brand b{color:var(--red);font-weight:700}
.menu-label{position:absolute;left:675px;top:30px;font-size:8px;font-weight:700;color:var(--white)}
.menu-btn{position:absolute;left:713px;top:20px;width:36px;height:30px;background:var(--red)}

.hero{position:absolute;left:0;top:72px;width:876px;height:444px;
  background:radial-gradient(ellipse at 45% 40%,#7a6a5c 0%,#4a3e36 35%,#2c2a26 70%,#1d1d1b 100%)}
.hero-title{position:absolute;left:126px;top:243px;font-size:25px;line-height:33px;color:var(--white);font-weight:400}
.hero-title .accent{color:var(--orange);font-weight:500}
.pager{position:absolute;left:127px;top:434px;display:flex;gap:6px;align-items:center}
.pager span{width:22px;height:22px;border-radius:50%;font-size:10px;font-weight:700;color:var(--white);display:flex;align-items:center;justify-content:center}
.pager .current{background:var(--red)}

.signup{position:absolute;left:535px;top:124px;width:222px;height:274px;border-radius:14px;background:rgba(110,8,12,.88);padding:0 8px}
.signup h2{font-size:20px;font-weight:500;color:var(--white);line-height:26px;padding:26px 0 10px 13px;border-bottom:1px solid rgba(255,255,255,.6)}
.signup label{display:block;font-size:8px;font-weight:600;color:var(--white);margin:18px 0 8px 5px}
.signup label + .field{margin-top:0}
.field{height:30px;border:1px solid rgba(255,255,255,.2);font-size:7px;color:#ddd;padding:11px 9px}
.signup .second{margin-top:13px}
.submit{margin:14px 0 0 4px;width:88px;height:22px;border-radius:11px;background:var(--orange);color:var(--white);font-size:10px;font-weight:600;display:flex;align-items:center;justify-content:center}

.tabs{position:absolute;left:0;top:516px;width:876px;height:82px;background:var(--red)}
.tab{position:absolute;top:32px;height:50px;display:flex;align-items:center;gap:9px;font-size:11px;font-weight:500;color:var(--white);padding:0 12px}
.tab.active{background:var(--grey-bg);color:#222}
.tab i{width:24px;height:24px;border-radius:50%;background:var(--white);display:block}
.tab.active i{background:#111}

.products{position:absolute;left:0;top:598px;width:876px;height:442px;background:var(--grey-bg)}
.section-title{position:absolute;left:0;width:876px;top:44px;text-align:center;font-size:22px;font-weight:500;color:var(--red)}
.btn-view{position:absolute;left:394px;top:85px;width:88px;height:22px;border-radius:11px;background:var(--orange);color:var(--white);font-size:11px;font-weight:500;display:flex;align-items:center;justify-content:center}
.card{position:absolute;top:140px;width:196px;height:188px;background:linear-gradient(#fff,#f4f4f4);box-shadow:0 2px 2px rgba(0,0,0,.1);text-align:center}
.card h3{font-size:14px;font-weight:500;line-height:18px;margin-top:20px;color:#555}
.price{font-size:35px;font-weight:700;color:var(--red);margin-top:6px;letter-spacing:-.5px}
.btn{display:flex;align-items:center;justify-content:center;gap:5px;margin:0 auto;width:100px;height:20px;font-size:7px;font-weight:600;color:var(--white)}
.btn-us{background:var(--red);margin-top:10px}
.btn-store{background:var(--orange);margin-top:6px}
.btn .sq{width:8px;height:8px;border:1.2px solid var(--white);border-radius:2px}
.bundle{position:absolute;top:361px;left:275px;display:flex;align-items:center}
.bundle .label{font-size:15px;color:#555;width:115px}
.bundle .price{margin:0 20px 0 0}
.bundle .btn{width:100px;background:var(--orange);margin:0}

.partners{position:absolute;left:0;top:1040px;width:876px;height:116px;border-bottom:1px solid var(--line)}
.partners-title{position:absolute;width:876px;top:30px;text-align:center;font-size:8px;color:#555}
.partner{position:absolute;top:62px;display:flex;align-items:center;gap:6px;font-size:22px;font-weight:700;letter-spacing:-.5px}
.partner i{width:20px;height:20px;border-radius:50%;display:block}
.p1{left:130px;color:#b3262a}.p1 i{background:#b3262a}
.p2{left:410px;color:#2a2f6e}.p2 i{background:#2a2f6e}
.p3{left:586px;color:#3b46b6}.p3 i{background:#3b46b6}
.copyright{position:absolute;left:0;width:876px;top:1173px;text-align:center;font-size:8px;color:#333}
</style>
</head>
<body>
<header class="site-header">
  <div class="brand"><b>Study</b> Along</div>
  <div class="menu-label">MENU</div>
  <div class="menu-btn">
    <svg width="36" height="30" viewBox="0 0 36 30"><g stroke="#fff" stroke-width="1.6"><line x1="13" y1="11" x2="23" y2="11"/><line x1="13" y1="15" x2="23" y2="15"/><line x1="13" y1="19" x2="23" y2="19"/></g></svg>
  </div>
</header>

<section class="hero" role="img" aria-label="Portrait photograph of the author against a blurred outdoor background">
</section>
<div class="hero-title abs" style="left:126px;top:315px"><span class="accent">Knowledge</span><br>to Boost<br>Your Career</div>
<div class="pager"><span class="current">1</span><span>2</span><span>3</span><span>4</span></div>

<form class="signup">
  <h2>Sign Up<br>For a Free Sample</h2>
  <label>First Name:</label>
  <div class="field">Enter Your First Name</div>
  <label>Email Address:</label>
  <div class="field">Enter Your E-mail ID</div>
  <div class="submit">SUBMIT</div>
</form>

<nav class="tabs">
  <div class="tab active" style="left:112px;width:194px"><i></i>Vectorial 1.5 &amp; Scaffoldr</div>
  <div class="tab" style="left:320px"><i></i>Vectorial 2 &amp; Scaffoldr</div>
  <div class="tab" style="left:516px"><i></i>Reactor</div>
</nav>

<main class="products">
  <h1 class="section-title">Vectorial 1.5 &amp; Scaffoldr</h1>
  <div class="btn-view">View App</div>

  <article class="card" style="left:127px">
    <h3>With Mock<br>Services</h3>
    <div class="price">$5.99</div>
    <div class="btn btn-us"><span class="sq"></span>BUY FROM US</div>
    <div class="btn btn-store"><span class="sq"></span>BUY FROM RIVERSTORE</div>
  </article>
  <article class="card" style="left:340px">
    <h3>With NodeForge<br>Services</h3>
    <div class="price">$5.99</div>
    <div class="btn btn-us"><span class="sq"></span>BUY FROM US</div>
    <div class="btn btn-store"><span class="sq"></span>BUY FROM RIVERSTORE</div>
  </article>
  <article class="card" style="left:553px">
    <h3>With FrostFusion<br>Services</h3>
    <div class="price">$5.99</div>
    <div class="btn btn-us"><span class="sq"></span>BUY FROM US</div>
    <div class="btn btn-store"><span class="sq"></span>BUY FROM RIVERSTORE</div>
  </article>

  <div class="bundle">
    <span class="label">Buy Them All</span>
    <span class="price">$9.99</span>
    <span class="btn"><span class="sq"></span>BUY FROM US</span>
  </div>
</main>

<section class="partners">
  <div class="partners-title">Our Partner's</div>
  <div class="partner p1"><i></i>NetPivot Consulting</div>
  <div class="partner p2"><i></i>Plumvane</div>
  <div class="partner p3"><i></i>Beyond The Grid</div>
</section>

<footer class="copyright">© 2016 Company Name &nbsp;|&nbsp; All Rights Reserved</footer>
</body>
</html>
```